New website for a business that provides behaviour analysis

A new website that details the services that are provided around behaviour analysis for people with a disability through QPKV. There also needs to incorporate an about us and a staff page, Plus a referral form that is a google doc.
The business already has a web address that needs to be tailored.
Soft colours are preferred.
Do not have lots of pictures, keep them minimal.
A logo for the business is also needed to be incorporated, and this is a separate project that can be awarded to the website winner.
Website needs to be able to be used on WIX who will be the host for the design.

Target Market(s)

QPKV clients requiring behaviour support clician

Industry/Entity Type

Clinical behaviour support and analysis

Colors
00AB8E
00BBA5
67D7C9
C6EFE9
E9F9F6

Requirements
Must have
• Soft colours, preferable pale turquoise, minimal pictures, clean, sophisticated and classical look

```html
<!DOCTYPE html>
<html lang="en">
<head>
<meta charset="utf-8">
<title>Behaviour Analysis</title>
<link rel="stylesheet" href="https://fonts.googleapis.com/css2?family=Montserrat:wght@400;500;600&display=swap">
<style>
:root{
  --green:#00AB8E;
  --green-2:#00BBA5;
  --mint:#67D7C9;
  --pale:#C6EFE9;
  --paler:#E9F9F6;
  --ink:#1d1d1d;
  --text:#333;
  --grey-bg:#f3f2f2;
  --tile:#f4f2f2;
  --black:#000;
  --white:#fff;
}
*{box-sizing:border-box;margin:0;padding:0}
html,body{width:1200px;height:3638px;overflow:hidden}
body{position:relative;font-family:"Montserrat",sans-serif;color:var(--text);background:var(--white)}
.abs{position:absolute}
.btn{position:absolute;display:flex;align-items:center;justify-content:center;background:var(--green);color:var(--white);font-weight:500;font-size:18px;border-radius:4px;text-decoration:none}

/* header + hero */
.hero-photo{left:0;top:0;width:1200px;height:559px;background:linear-gradient(100deg,#d9c8ae 0%,#9fb0b3 25%,#8e8a7c 55%,#6f6557 80%,#bfa886 100%)}
.hero-shade{left:580px;top:0;width:620px;height:559px;background:linear-gradient(90deg,rgba(0,0,0,0),rgba(0,0,0,.18))}
.logo{left:130px;top:18px;font-size:27px;font-weight:500;color:var(--green)}
.nav{left:484px;top:27px;display:flex;gap:37px;font-size:13px;color:var(--white)}
.nav .active{color:var(--green)}
.support{left:963px;top:0;width:237px;height:70px;background:var(--green);color:var(--white);font-size:12.5px;font-weight:500;text-align:right;padding:16px 78px 0 0;line-height:26px}
.support svg{position:absolute;right:20px;top:16px}
.hero-kicker{left:623px;top:190px;font-size:36px;font-weight:500;color:var(--white)}
.hero-title{left:623px;top:242px;font-size:51px;font-weight:500;color:#ececec}
.hero-text{left:623px;top:316px;width:460px;font-size:14px;line-height:35px;color:var(--white)}
.hero-btn{left:623px;top:408px;width:169px;height:47px}
.sq1{left:1086px;top:328px;width:114px;height:114px;background:linear-gradient(135deg,#fff,#eee)}
.sq2{left:974px;top:442px;width:112px;height:117px;background:linear-gradient(180deg,#f3f3f3,#fff)}
.scroll{left:131px;top:541px;width:40px;height:40px;border-radius:50%;background:var(--green)}

/* about */
.about-bg{left:0;top:559px;width:1200px;height:692px;background:linear-gradient(180deg,#fff 0%,#f2f2f2 100%)}
.stripes{background:repeating-linear-gradient(135deg,#e2e2e2 0 5px,transparent 5px 11px)}
.about-stripe{left:537px;top:1045px;width:148px;height:152px}
.about-card{left:137px;top:731px;width:520px;height:441px;background:var(--white);box-shadow:0 2px 12px rgba(0,0,0,.1);padding:36px 32px}
.h-section{font-size:24px;font-weight:500;color:var(--green)}
.about-card h2{display:flex;align-items:center;gap:14px}
.about-card h2::after{content:"";width:44px;height:2px;background:var(--green)}
.about-card p{margin-top:14px;font-size:14.5px;line-height:34.6px;color:var(--ink);width:370px}
.about-card .btn{left:32px;top:349px;width:138px;height:48px}
.about-frame{left:648px;top:661px;width:414px;height:293px;border:4px solid var(--green)}
.about-photo{left:556px;top:673px;width:490px;height:372px;background:linear-gradient(135deg,#3b3f3a,#7a776b 45%,#b6a48c 75%,#5a5a55)}

/* services */
.services-title{left:0;top:1330px;width:1200px;text-align:center;font-size:29px}
.svc-feature{left:131px;top:1423px;width:225px;height:342px;background:var(--green);color:var(--white);padding:24px 22px}
.svc-feature h3{margin-top:18px;font-size:17px;font-weight:500}
.svc-feature p{margin-top:8px;font-size:14px;line-height:34.6px}
.svc-feature .rule{position:absolute;left:22px;right:24px;top:276px;height:1px;background:rgba(255,255,255,.7)}
.svc-feature .more{position:absolute;left:22px;right:24px;top:295px;display:flex;justify-content:space-between;font-size:15px;font-weight:500}
.tile{width:211px;height:142px;background:var(--tile);padding:34px 26px 0}
.tile span{display:block;margin-top:18px;font-size:15px;color:var(--ink)}

/* staff */
.staff-band{left:0;top:1852px;width:1067px;height:309px;background:var(--green)}
.staff-title{left:131px;top:1918px;font-size:29px;font-weight:500;color:var(--white)}
.arrow-btn{top:1920px;width:35px;height:35px}
.staff-photo{top:2013px;width:239px;height:274px}
.staff-name{top:2316px;width:239px;text-align:center;font-size:19px;font-weight:500;color:var(--ink)}

/* locations */
.loc-title{left:131px;top:2434px;font-size:29px}
.loc-text{left:131px;top:2484px;width:305px;font-size:14.5px;line-height:34.6px;color:var(--ink)}
.loc-btn{left:133px;top:2755px;width:163px;height:46px}
.map{left:460px;top:2430px;width:607px;height:387px;border:2px solid var(--green);padding:7px}
.map div{width:100%;height:100%;background:linear-gradient(135deg,#eef0f2 0%,#e6e9ec 45%,#f3ebc6 70%,#e8eaed 100%)}

/* quote */
.dark{left:0;top:3076px;width:1200px;height:562px;background:var(--black)}
.quote-photo{left:662px;top:2906px;width:390px;height:345px;background:linear-gradient(135deg,#e7e4df,#8a7d72 50%,#4a3e3a)}
.quote-frame{left:148px;top:2929px;width:276px;height:293px;border:4px solid var(--green)}
.quote-stripe{left:600px;top:3290px;width:148px;height:64px;background:repeating-linear-gradient(135deg,#3a3a3a 0 5px,transparent 5px 11px)}
.quote-card{left:167px;top:2949px;width:567px;height:383px;background:var(--white)}
.quote-card h2{position:absolute;top:40px;width:100%;text-align:center;font-size:29px}
.field{position:absolute;width:260px;height:36px;border-bottom:1px solid #777;font-size:14px;color:var(--ink)}
.quote-card .btn{left:203px;top:291px;width:162px;height:47px}

/* footer */
.f-brand{left:0;top:3393px;width:1200px;text-align:center;font-size:27px;font-weight:500;color:var(--white)}
.f-nav{left:0;top:3461px;width:1200px;display:flex;justify-content:center;gap:37px;font-size:14px;font-weight:500;color:var(--white)}
.socials{left:543px;top:3508px;display:flex;gap:7px}
.socials span{width:33px;height:33px;border:2px solid var(--white);border-radius:50%}
.f-rule{left:131px;top:3572px;width:936px;height:1px;background:#444}
.copy{left:0;top:3596px;width:1200px;text-align:center;font-size:12px;color:var(--white)}
.to-top{left:1067px;top:3558px;width:40px;height:40px;border-radius:50%;background:var(--green)}
</style>
</head>
<body>

<!-- Hero -->
<div class="abs hero-photo" role="img" aria-label="Smiling woman in a wheelchair on a sunny beach"></div>
<div class="abs hero-shade"></div>
<div class="abs logo">Behaviour Analysis</div>
<nav class="abs nav"><span class="active">HOME</span><span>ABOUT US</span><span>OUR STAFF</span><span>CONTACT US</span></nav>
<div class="abs support">CUSTOMER SUPPORT<br>+1 555 010 2040
  <svg width="34" height="36" viewBox="0 0 34 36" fill="none" stroke="#fff" stroke-width="1.6"><circle cx="17" cy="13" r="8"/><path d="M8 13a9 9 0 0 1 18 0M7 12v5M27 12v5M27 17q0 5-7 5"/><path d="M3 35q1-10 14-10t14 10z"/></svg>
</div>
<div class="abs hero-kicker">Welcome to</div>
<div class="abs hero-title">Behaviour Analysis</div>
<p class="abs hero-text">Lorem ipsum dolor sit amet, consectetur adipiscing elit, sed do eiusmod tempor incididunt.</p>
<a class="btn hero-btn">Referral Form</a>
<div class="abs sq1"></div>
<div class="abs sq2"></div>
<div class="abs scroll"></div>
<svg class="abs" style="left:144px;top:560px" width="14" height="34" viewBox="0 0 14 34" fill="none" stroke="#000" stroke-width="1.6"><path d="M7 0v32M1 26l6 6 6-6"/></svg>

<!-- About -->
<div class="abs about-bg"></div>
<div class="abs stripes about-stripe"></div>
<section class="abs about-card">
  <h2 class="h-section">About Us</h2>
  <p>Sed ut perspiciatis unde omnis iste natus error sit voluptatem accusantium doloremque laudantium, totam rem aperiam, eaque ipsa quae ab illo inventore veritatis et quasi architecto beatae vitae dicta sunt explicabo. Nemo enim ipsam voluptatem quia voluptas sit aspernatur aut odit aut fugit.</p>
  <a class="btn">Learn More</a>
</section>
<div class="abs about-frame"></div>
<div class="abs about-photo" role="img" aria-label="Colleagues laughing around a table, one in a wheelchair"></div>

<!-- Services -->
<h2 class="abs h-section services-title">Our Services</h2>
<div class="abs svc-feature">
  <svg width="44" height="48" viewBox="0 0 44 48" fill="none" stroke="#fff" stroke-width="1.8"><circle cx="22" cy="5" r="3.5"/><path d="M20 12v14h12l5 12M20 18h9"/><path d="M15 20a12 12 0 1 0 14 20"/></svg>
  <h3>Lorem ipsum dolor</h3>
  <p>Sed ut perspiciatis unde omnis iste natus error sit voluptatem accusantium totam rem</p>
  <div class="rule"></div>
  <div class="more"><span>View All</span><span>&#8594;</span></div>
</div>

<div class="abs tile" style="left:376px;top:1440px">
  <svg width="40" height="34" viewBox="0 0 40 34" fill="none" stroke="#333" stroke-width="1.5"><path d="M20 32 5 18A9 9 0 0 1 20 6a9 9 0 0 1 15 12z"/><path d="M12 18l6 6M16 15l6 6M22 13l5 5"/></svg>
  <span>Sed ut perspiciatis</span></div>
<div class="abs tile" style="left:616px;top:1440px">
  <svg width="40" height="34" viewBox="0 0 40 34" fill="none" stroke="#333" stroke-width="1.5"><circle cx="12" cy="12" r="4"/><circle cx="28" cy="12" r="4"/><circle cx="20" cy="20" r="4"/><path d="M4 26q0-7 8-7M36 26q0-7-8-7M12 33q0-7 8-7t8 7"/></svg>
  <span>Sed ut perspiciatis</span></div>
<div class="abs tile" style="left:854px;top:1440px">
  <svg width="40" height="34" viewBox="0 0 40 34" fill="none" stroke="#333" stroke-width="1.5"><circle cx="20" cy="10" r="8"/><circle cx="20" cy="9" r="3"/><path d="M4 22l8-3 8 5 8-5 8 3M6 30h28"/></svg>
  <span>Sed ut perspiciatis</span></div>
<div class="abs tile" style="left:376px;top:1607px">
  <svg width="40" height="34" viewBox="0 0 40 34" fill="none" stroke="#333" stroke-width="1.5"><circle cx="20" cy="6" r="4"/><circle cx="9" cy="26" r="4"/><circle cx="31" cy="26" r="4"/><path d="M20 10v6M14 22l6-6 6 6M3 33q0-3 6-3t6 3M25 33q0-3 6-3t6 3"/></svg>
  <span>Sed ut perspiciatis</span></div>
<div class="abs tile" style="left:616px;top:1607px">
  <svg width="40" height="34" viewBox="0 0 40 34" fill="none" stroke="#333" stroke-width="1.5"><circle cx="20" cy="8" r="5"/><circle cx="8" cy="13" r="4"/><circle cx="32" cy="13" r="4"/><path d="M10 30q0-12 10-12t10 12zM2 28q0-8 7-8M38 28q0-8-7-8"/></svg>
  <span>Sed ut perspiciatis</span></div>
<div class="abs tile" style="left:854px;top:1607px">
  <svg width="40" height="34" viewBox="0 0 40 34" fill="none" stroke="#333" stroke-width="1.5"><path d="M20 22 11 13a6 6 0 0 1 9-8 6 6 0 0 1 9 8z"/><path d="M4 8v14l8 8M36 8v14l-8 8"/></svg>
  <span>Sed ut perspiciatis</span></div>

<!-- Staff -->
<div class="abs staff-band"></div>
<h2 class="abs staff-title">Meet Our Staff Members</h2>
<svg class="abs arrow-btn" style="left:889px" viewBox="0 0 35 35" fill="none" stroke="#fff" stroke-width="2"><circle cx="17.5" cy="17.5" r="16"/><path d="M26 17.5H10M16 11l-6 6.5 6 6.5"/></svg>
<svg class="abs arrow-btn" style="left:946px" viewBox="0 0 35 35" fill="none" stroke="#fff" stroke-width="2"><circle cx="17.5" cy="17.5" r="16"/><path d="M9 17.5h16M19 11l6 6.5-6 6.5"/></svg>
<div class="abs staff-photo" style="left:133px;background:linear-gradient(180deg,#ececec,#d9dcdf 55%,#6a8da9)" role="img" aria-label="Staff member portrait"></div>
<div class="abs staff-photo" style="left:377px;background:linear-gradient(180deg,#efefef,#dddad6 45%,#4b4b4b)" role="img" aria-label="Staff member portrait"></div>
<div class="abs staff-photo" style="left:621px;background:linear-gradient(180deg,#e4e6e9,#c9ccd0 45%,#1e2433)" role="img" aria-label="Staff member portrait"></div>
<div class="abs staff-photo" style="left:865px;background:linear-gradient(180deg,#aedae7,#c3e4ec 45%,#e9edee)" role="img" aria-label="Staff member portrait"></div>
<div class="abs staff-name" style="left:133px">Lorem Ipsum</div>
<div class="abs staff-name" style="left:377px">Lorem Ipsum</div>
<div class="abs staff-name" style="left:621px">Lorem Ipsum</div>
<div class="abs staff-name" style="left:865px">Lorem Ipsum</div>

<!-- Locations -->
<h2 class="abs h-section loc-title">Our Locations</h2>
<p class="abs loc-text">Lorem ipsum dolor sit amet, consectetur adipiscing elit, sed do eiusmod tempor incididunt ut labore et dolore magna aliqua. Ut enim ad minim veniam, quis nostrud exercitation ullamco laboris nisi ut aliquip ex ea commodo consequat. voluptate velit esse.</p>
<a class="btn loc-btn">View Locations</a>
<div class="abs map"><div role="img" aria-label="Street map showing office location"></div></div>

<!-- Quote -->
<div class="abs dark"></div>
<div class="abs quote-photo" role="img" aria-label="Three women reviewing a tablet together"></div>
<div class="abs quote-frame"></div>
<div class="abs quote-stripe"></div>
<form class="abs quote-card">
  <h2 class="h-section">Request A Quote</h2>
  <div class="field" style="left:15px;top:102px">Name</div>
  <div class="field" style="left:295px;top:102px">Email Address</div>
  <div class="field" style="left:15px;top:165px">Subject</div>
  <div class="field" style="left:295px;top:165px">Phone Number</div>
  <div class="field" style="left:15px;top:227px;width:540px">Message</div>
  <a class="btn">Submit Now</a>
</form>

<!-- Footer -->
<div class="abs f-brand">Behaviour Analysis</div>
<nav class="abs f-nav"><span>HOME</span><span>ABOUT US</span><span>OUR STAFF</span><span>CONTACT US</span></nav>
<div class="abs socials"><span aria-label="Social link"></span><span aria-label="Social link"></span><span aria-label="Social link"></span></div>
<div class="abs f-rule"></div>
<div class="abs copy">© 2024 COPYRIGHTS. ALL RIGHTS RESERVED</div>
<div class="abs to-top"></div>
<svg class="abs" style="left:1080px;top:3544px" width="14" height="34" viewBox="0 0 14 34" fill="none" stroke="#fff" stroke-width="1.6"><path d="M7 34V2M1 8l6-6 6 6"/></svg>

</body>
</html>
```